Website for IT consulting Company

I need a website upgrade, the existing site content is ok, I would also like to add a testimonial page, the site should be something that is easy for us to update content. You use the content from www.kelvanbrook.com as an example. I will also post update logo and artwork. I also need a contact form with some type of validation or captcha.

I added Coded to the Project

Please omit Address maps

Target Market(s)

small business, service oriented companies. We provide IT Consulting, support and mangement

Industry/Entity Type

Information Technology

Coding

Number of Pages Required

1 page

Font styles to use
Serif
Sans Serif

Requirements
Must have
• Contain logo attached, and content from existing web site www.kelvanbrook.com.
• Also need to update content easily, and be movable to different platforms.
• There is a catch phrase
• "Let us worry about your technology…” “ so you don’t have to!”
• Should be included.
Nice to have
• Testimonial page, Project page where we can post new and past projects and pictures
Should not have
• none

```html
<!DOCTYPE html>
<html lang="en">
<head>
<meta charset="utf-8">
<title>Kelvanbrook – IT Solutions</title>
<link href="https://fonts.googleapis.com/css2?family=Lato:wght@400;700;900&family=Raleway:wght@400;500;600;700&display=swap" rel="stylesheet">
<style>
:root{
  --blue:#1a7fc4;
  --blue-dark:#1468a3;
  --ink:#2b2b2b;
  --text:#444;
  --grey-bar:#3d3d3d;
  --footer:#474747;
  --light:#f5f5f5;
  --white:#fff;
  --btn-grey:#6a6a6a;
}
*{box-sizing:border-box;margin:0;padding:0}
html,body{width:1200px;height:3327px;overflow:hidden}
body{position:relative;font-family:"Raleway",Arial,sans-serif;color:var(--text);background:var(--white)}
.abs{position:absolute}
h2,h3,h4{font-family:"Lato",Arial,sans-serif;color:var(--ink)}

/* top bar */
.topbar{left:0;top:0;width:1200px;height:27px;background:var(--grey-bar);color:var(--white);font-size:14px;font-weight:600}
.topbar .item{position:absolute;top:5px;display:flex;align-items:center;gap:8px}
.topbar .social{position:absolute;right:80px;top:5px;display:flex;gap:8px}
.dot{width:17px;height:17px;border-radius:50%;background:var(--white)}

/* header */
.header{left:0;top:27px;width:1200px;height:133px;background:var(--white)}
.brand{position:absolute;left:90px;top:40px;display:flex;align-items:center;gap:12px}
.brand-square{width:46px;height:46px;background:var(--blue)}
.brand-name{font-family:"Lato",Arial,sans-serif;font-weight:900;font-size:40px;color:#555;letter-spacing:1px}
.brand-tag{position:absolute;left:148px;top:90px;font-size:10px;color:var(--blue)}
.nav{position:absolute;right:88px;top:64px;display:flex;gap:38px;font-family:"Lato",Arial,sans-serif;font-weight:700;font-size:15px;color:var(--ink)}

/* hero */
.hero{left:0;top:160px;width:1200px;height:443px;background:linear-gradient(100deg,#2d3f52 0%,#6f8397 40%,#b9c6d2 60%,#3b4a5a 100%)}
.hero-title{position:absolute;left:0;top:258px;width:1200px;text-align:center;font-family:"Lato",Arial,sans-serif;font-weight:700;font-size:24px;line-height:33px;color:var(--white)}
.btn-light{position:absolute;left:528px;top:339px;width:162px;height:47px;background:var(--white);border-radius:4px;text-align:center;line-height:47px;font-size:12px;font-weight:700;letter-spacing:1px;color:var(--ink)}
.dots{position:absolute;left:563px;top:410px;display:flex;gap:8px}
.dots span{width:13px;height:13px;border-radius:50%;background:var(--white)}
.dots span.active{background:var(--blue)}

/* welcome */
.welcome{left:0;top:603px;width:1200px;height:311px}
.welcome h2{position:absolute;top:48px;width:1200px;text-align:center;font-size:29px;letter-spacing:2px;font-weight:700}
.welcome p{position:absolute;left:96px;top:105px;width:1008px;text-align:center;font-size:16px;line-height:29px;color:#333}
.btn-grey{position:absolute;left:547px;top:240px;width:140px;height:38px;background:var(--btn-grey);border-radius:3px;color:var(--white);text-align:center;line-height:38px;font-size:14px;font-weight:600}

/* services */
.services{left:0;top:914px;width:1200px;height:492px;background:var(--blue)}
.service{position:absolute;top:0;width:330px;text-align:center;color:var(--white)}
.service .icon{position:absolute;left:114px;top:68px;width:104px;height:104px}
.service h3{position:absolute;top:210px;width:330px;color:var(--white);font-size:15px;font-weight:700}
.service p{position:absolute;left:20px;top:242px;width:290px;font-size:14px;line-height:23px}
.btn-white{position:absolute;left:85px;top:354px;width:160px;height:49px;background:var(--white);border-radius:3px;color:var(--blue);line-height:49px;font-weight:700;font-size:14px}

/* solutions */
.solutions{left:0;top:1406px;width:1200px;height:541px}
.solutions h3{position:absolute;font-size:20px;font-weight:700;letter-spacing:.5px;line-height:25px}
.rule{position:absolute;width:66px;height:3px;background:var(--blue)}
.photo{position:absolute}
.list{position:absolute;left:315px;top:162px;list-style:none;font-size:14px;line-height:29px;color:#333}
.btn-blue{position:absolute;width:158px;height:47px;background:var(--blue);border-radius:3px;color:var(--white);text-align:center;line-height:47px;font-weight:700;font-size:14px}
.side-text{position:absolute;left:887px;top:152px;width:218px;font-size:15px;line-height:29px;text-align:justify;color:#333}
.wide-text{position:absolute;left:641px;top:333px;width:465px;font-size:15px;line-height:29px;color:#333}

/* testimonials */
.testimonials{left:0;top:1947px;width:1200px;height:564px;background:var(--light)}
.testimonials h2{position:absolute;top:50px;width:1200px;text-align:center;font-size:20px;font-weight:700;letter-spacing:1px}
.card{position:absolute;top:0;width:340px;text-align:center}
.avatar{position:absolute;left:77px;top:103px;width:186px;height:186px;border-radius:50%;background:radial-gradient(circle at 50% 40%,#9a9a9a,#3e3e3e)}
.card h4{position:absolute;top:318px;width:340px;font-size:21px;letter-spacing:1px;font-weight:400}
.card h4 b{font-weight:900}
.card p{position:absolute;left:20px;top:348px;width:300px;font-size:15.5px;line-height:25px;color:#333}
.card .link{position:absolute;top:425px;width:340px;font-size:15px;color:var(--blue)}
.card .more{position:absolute;top:458px;width:340px;font-size:14px;color:#333;display:flex;justify-content:center;align-items:center;gap:6px}

/* quote band */
.quote{left:0;top:2511px;width:1200px;height:350px;background:linear-gradient(90deg,#8fbde0 0%,#8fbde0 35%,#9cb7cf 60%,#6d8aa6 100%)}
.quote p{position:absolute;left:134px;top:100px;width:420px;text-align:center;font-family:"Lato",Arial,sans-serif;font-weight:900;font-size:32px;line-height:34px;color:var(--white)}

/* newsletter */
.newsletter{left:0;top:2861px;width:1200px;height:213px}
.newsletter h2{position:absolute;top:58px;width:1200px;text-align:center;font-size:24px;font-weight:700;letter-spacing:1.5px}
.newsletter .sub{position:absolute;top:94px;width:1200px;text-align:center;font-family:"Lato",Arial,sans-serif;font-size:13px;letter-spacing:1px;color:var(--ink)}
.field{position:absolute;left:333px;top:147px;width:423px;height:23px;border:1px solid #ddd;background:var(--white);font-size:10px;color:#777;padding:5px 8px}
.submit{position:absolute;left:756px;top:147px;width:96px;height:23px;background:var(--blue);color:var(--white);text-align:center;line-height:23px;font-size:13px;font-weight:700;letter-spacing:1px}

/* footer */
.footer{left:0;top:3074px;width:1200px;height:215px;background:var(--footer);color:var(--white)}
.fcol{position:absolute;top:30px}
.fcol h4{color:var(--white);font-size:17px;font-weight:900;letter-spacing:.5px}
.fcol .u{width:50px;height:2px;background:var(--white);margin:6px 0 12px}
.fcol ul{list-style:none;font-size:14px;font-weight:600;line-height:30px}
.fsocial{display:flex;gap:10px}
.fsocial span{width:20px;height:20px;border-radius:50%;background:var(--white)}
.copyright{left:0;top:3289px;width:1200px;height:38px;background:var(--blue);color:var(--white);text-align:center;line-height:38px;font-size:13px;font-weight:600;letter-spacing:.5px}
</style>
</head>
<body>

<div class="abs topbar">
  <div class="item" style="left:95px">
    <svg width="12" height="16" viewBox="0 0 12 16"><path d="M6 0a6 6 0 0 0-6 6c0 4.5 6 10 6 10s6-5.5 6-10a6 6 0 0 0-6-6zm0 8.5A2.5 2.5 0 1 1 6 3.5a2.5 2.5 0 0 1 0 5z" fill="#fff"/></svg>
    123 Street, City Name, DC 12345
  </div>
  <div class="item" style="left:410px">
    <svg width="16" height="12" viewBox="0 0 16 12"><rect width="16" height="12" fill="#fff"/><path d="M0 0l8 6 8-6" stroke="#3d3d3d" fill="none" stroke-width="1.5"/></svg>
    info@kelvanbrook.com
  </div>
  <div class="item" style="left:600px">
    <svg width="14" height="14" viewBox="0 0 14 14"><path d="M3 0l3 3-2 2c1 2 3 4 5 5l2-2 3 3-2 3C6 14 0 8 0 2z" fill="#fff"/></svg>
    123-4567-8910
  </div>
  <div class="social"><span class="dot"></span><span class="dot"></span><span class="dot"></span><span class="dot"></span><span class="dot"></span></div>
</div>

<header class="abs header">
  <div class="brand"><span class="brand-square"></span><span class="brand-name">KELVANBROOK</span></div>
  <div class="brand-tag">IT consulting, support and management</div>
  <nav class="nav"><span>ABOUT</span><span>CONTACT</span><span>SUPPORT</span><span>CLIENTS</span><span>CAREERS</span></nav>
</header>

<section class="abs hero" role="img" aria-label="Business handshake photo with a tablet in hand">
  <h1 class="hero-title">IT SOLUTIONS THAT WORK FOR YOUR BUSINESS.<br>A FULL SERVICE TECHNOLOGY COMPANY.</h1>
  <div class="btn-light">READ MORE</div>
  <div class="dots"><span class="active"></span><span></span><span></span><span></span></div>
</section>

<section class="abs welcome">
  <h2>WELCOME TO KELVANBROOK</h2>
  <p>Outsourcing is subcontracting a process, such as product design or manufacturing, to a third-party company.[1] The decision to outsource is often made in the interest of lowering firm costs, redirecting or conserving energy directed at the competencies of a particular business, or to make more efficient use of land, labor, capital, (information) technology and resources. Outsourcing became part of the business lexicon during the 1980s</p>
  <div class="btn-grey">Read More</div>
</section>

<section class="abs services">
  <div class="service" style="left:83px">
    <svg class="icon" viewBox="0 0 104 104"><circle cx="52" cy="52" r="49" fill="none" stroke="#fff" stroke-width="4"/><circle cx="52" cy="40" r="9" fill="#fff"/><path d="M34 66c4-10 32-10 36 0" fill="#fff"/><path d="M30 52h44" stroke="#fff" stroke-width="3"/></svg>
    <h3>MANAGED IT SOLUTIONS</h3>
    <p>Our staff will design, service, administer and maintain your IT needs. We are well versed on all major operating system, and network appliances...</p>
    <div class="btn-white">READ MORE</div>
  </div>
  <div class="service" style="left:429px">
    <svg class="icon" viewBox="0 0 104 104"><circle cx="52" cy="52" r="49" fill="none" stroke="#fff" stroke-width="4"/><path d="M36 70l20-20" stroke="#fff" stroke-width="6" stroke-linecap="round"/><path d="M56 38a14 14 0 0 1 12 12M58 28a24 24 0 0 1 20 20" stroke="#fff" stroke-width="3" fill="none"/></svg>
    <h3>REMOTE DIAGNOSTIC &amp;SUPPORT</h3>
    <p>Do you need a quick solution to a technical problem? With our live remote-assistance tool, a member of our support team can view your desktop and share control...</p>
    <div class="btn-white">READ MORE</div>
  </div>
  <div class="service" style="left:804px">
    <svg class="icon" viewBox="0 0 104 104"><circle cx="52" cy="52" r="49" fill="none" stroke="#fff" stroke-width="4"/><circle cx="52" cy="52" r="20" fill="none" stroke="#fff" stroke-width="3"/><path d="M32 52h40M52 32v40" stroke="#fff" stroke-width="2"/><ellipse cx="52" cy="52" rx="9" ry="20" fill="none" stroke="#fff" stroke-width="2"/></svg>
    <h3>IT INFRASTRUCTURE DESIGN</h3>
    <p>Do you have more than one site? Do you need remote access? We can design and implement LANS/WANS and VPN's. Make your ...</p>
    <div class="btn-white">READ MORE</div>
  </div>
</section>

<section class="abs solutions">
  <h3 style="left:102px;top:70px">IT SUPPORT SOLUTIONS</h3>
  <div class="rule" style="left:102px;top:108px"></div>
  <div class="photo" role="img" aria-label="Smiling IT support technician" style="left:100px;top:153px;width:184px;height:255px;background:linear-gradient(180deg,#e9ecef,#a9b0b6)"></div>
  <ul class="list">
    <li>NETWORK ADMINISTRATION.</li><li>• DESKTOP SUPPORT.</li><li>• TELECOMMUNICATIONS.</li><li>• DISASTER RECOVERY.</li><li>• AUDIO/VIDEO MULTIMEDIA.</li><li>• WEB DESIGN.</li><li>•NETWORK CABLING.</li><li>• WIRELESS NETWORKS.</li><li>• ANTIVIRUS SOLUTIONS</li>
  </ul>
  <div class="btn-blue" style="left:100px;top:455px">READ MORE</div>

  <h3 style="left:641px;top:80px">FLEXIBLE SOLUTIONS FOR YOUR<br>BUSINESS NEEDS</h3>
  <div class="photo" role="img" aria-label="Engineer working beside server racks" style="left:641px;top:153px;width:157px;height:149px;background:linear-gradient(90deg,#d8dde2,#5c6670)"></div>
  <p class="side-text">Kelvanbrook is a technology solution provider based in Millbrook, Oregon. Our goal is to make technology a non-issue for individuals and small to medium size businesses</p>
  <p class="wide-text">ranging from 5 to 150 Users. Kelvanbrook has the experience, the tools, high-level technology solutions and training to power your business and your work force. We understand that all business's have one goal in common!</p>
  <div class="btn-blue" style="left:643px;top:455px">READ MORE</div>
</section>

<section class="abs testimonials">
  <h2>TESTIMONIAL</h2>
  <div class="card" style="left:70px">
    <div class="avatar" role="img" aria-label="Client portrait"></div>
    <h4><b>NAME,</b> DIRECTOR</h4>
    <p>"Lorem ipsum dolor amet conse ctetur<br>dolore elit,sed do eiusmod tempor<br>et dolore magna."</p>
    <div class="link">Lorem ipsum dolor</div>
    <div class="more">read more... <svg width="18" height="18" viewBox="0 0 18 18"><circle cx="9" cy="9" r="8" fill="none" stroke="#333" stroke-width="1.5"/><path d="M5 9h7M9 6l3 3-3 3" stroke="#333" stroke-width="1.5" fill="none"/></svg></div>
  </div>
  <div class="card" style="left:434px">
    <div class="avatar" role="img" aria-label="Client portrait" style="background:radial-gradient(circle at 50% 40%,#e0b48f,#6a5040)"></div>
    <h4><b>NAME,</b> DIRECTOR</h4>
    <p>"Lorem ipsum dolor amet conse ctetur<br>dolore elit,sed do eiusmod tempor<br>et dolore magna."</p>
    <div class="link">Lorem ipsum dolor</div>
    <div class="more">read more... <svg width="18" height="18" viewBox="0 0 18 18"><circle cx="9" cy="9" r="8" fill="none" stroke="#333" stroke-width="1.5"/><path d="M5 9h7M9 6l3 3-3 3" stroke="#333" stroke-width="1.5" fill="none"/></svg></div>
  </div>
  <div class="card" style="left:796px">
    <div class="avatar" role="img" aria-label="Client portrait"></div>
    <h4><b>NAME,</b> DIRECTOR</h4>
    <p>"Lorem ipsum dolor amet conse ctetur<br>dolore elit,sed do eiusmod tempor<br>et dolore magna."</p>
    <div class="link">Lorem ipsum dolor</div>
    <div class="more">read more... <svg width="18" height="18" viewBox="0 0 18 18"><circle cx="9" cy="9" r="8" fill="none" stroke="#333" stroke-width="1.5"/><path d="M5 9h7M9 6l3 3-3 3" stroke="#333" stroke-width="1.5" fill="none"/></svg></div>
  </div>
</section>

<section class="abs quote" role="img" aria-label="Business team meeting around a laptop, tinted blue">
  <p>“LET US WORRY ABOUT<br>YOUR<br>TECHNOLOGY...”<br>“ SO YOU DON’T HAVE TO!”</p>
</section>

<section class="abs newsletter">
  <h2>SUBSCRIBE TO OUR NEWSLETTER</h2>
  <div class="sub">TO RECEIVE THE LATEST NEWS &amp; UPDATE</div>
  <div class="field">Your E-Mail</div>
  <div class="submit">SUBMIT</div>
</section>

<footer class="abs footer">
  <div class="fcol" style="left:124px">
    <h4>ABOUT US</h4><div class="u"></div>
    <ul><li>Contact</li><li>Support</li><li>Clients</li><li>Careers</li></ul>
  </div>
  <div class="fcol" style="left:490px">
    <h4>CONTACT</h4><div class="u"></div>
    <ul><li>123 Street, City Name, DC 12345</li><li>123-4567-8910</li><li>info@kelvanbrook.com</li></ul>
  </div>
  <div class="fcol" style="left:900px">
    <h4>QUICK LINKS</h4><div class="u"></div>
    <div class="fsocial"><span></span><span></span><span></span><span></span><span></span></div>
  </div>
</footer>
<div class="abs copyright">Copyright © 2007 - Kelvanbrook Development Group, Inc - All rights reserved</div>

</body>
</html>
```